TalkHarbor - Language Coaching Services

Sleek, innovative, trendy design for Language Coaching business.

TalkHarbor is a new UK based company that provides Language Coaching services. We offer highly personalized on-line and face to face language courses. We also impart learning techniques workshops based on the latest neuroscience research for second-language acquisition.

Target Market(s)

See attached info

Industry/Entity Type

Consulting

Contact Information for Business Card

TalkHarbor
DaniaKV@talkharbor.co.uk
TalkHarbor.co.uk
London, UK

Font styles to use
Sans Serif

```html
<!DOCTYPE html>
<html lang="en">
<head>
<meta charset="utf-8">
<title>TalkHarbor Business Card</title>
<link rel="stylesheet" href="https://fonts.googleapis.com/css2?family=Montserrat:wght@400;600&family=Lato:wght@400&display=swap">
<style>
  :root {
    --backdrop: #3a3a3c;
    --card-white: #ffffff;
    --brand-blue: #0a8fd0;
    --brand-sky: #00a9e2;
    --brand-deep: #0a6fa3;
    --ink: #1e1e1e;
    --muted: #4a4a4a;
    --rule: #a8a8c0;
  }
  * { box-sizing: border-box; margin: 0; padding: 0; }
  html, body { width: 1200px; height: 1200px; overflow: hidden; }
  body {
    background: var(--backdrop);
    position: relative;
    font-family: "Lato", sans-serif;
  }
  .card {
    position: absolute;
    top: 310px;
    height: 594px;
    box-shadow: 0 4px 10px rgba(0,0,0,0.45);
    text-align: center;
  }
  .card--front { left: 234px; width: 364px; background: var(--card-white); }
  .card--back {
    left: 627px; width: 369px;
    background: linear-gradient(180deg, var(--brand-sky) 0%, var(--brand-sky) 36%, var(--brand-deep) 36%, var(--brand-deep) 100%);
    overflow: hidden;
  }
  .brand-circle {
    position: absolute; left: 125px; top: 90px;
    width: 114px; height: 114px; border-radius: 50%;
    border: 7px solid var(--brand-blue);
  }
  .brand-name {
    position: absolute; left: 0; right: 0; top: 212px;
    font-family: "Montserrat", sans-serif; font-weight: 400;
    font-size: 36px; letter-spacing: 1px;
    color: var(--brand-blue);
  }
  .holder-name {
    position: absolute; left: 0; right: 0; top: 338px;
    font-family: "Montserrat", sans-serif; font-size: 20px;
    color: var(--brand-blue);
  }
  .holder-name strong { font-weight: 600; }
  .holder-role {
    position: absolute; left: 0; right: 0; top: 360px;
    font-size: 16px; color: var(--muted);
  }
  .divider { position: absolute; left: 0; width: 364px; }
  .divider--icons { top: 394px; }
  .divider--place { top: 508px; }
  .contact-list {
    position: absolute; left: 0; right: 0; top: 431px;
    list-style: none; font-size: 17px; line-height: 22px; color: var(--ink);
  }
  .location {
    position: absolute; left: 0; right: 0; top: 536px;
    font-size: 17px; color: var(--ink);
  }
  .back-mark {
    position: absolute; left: 0; top: 108px;
    width: 369px; height: 380px;
  }
  .back-name {
    position: absolute; left: 0; right: 0; top: 278px;
    font-family: "Montserrat", sans-serif; font-weight: 400;
    font-size: 36px; color: var(--card-white); letter-spacing: 1px;
  }
  .back-url {
    position: absolute; left: 0; right: 0; top: 524px;
    font-size: 17px; color: var(--card-white);
  }
</style>
</head>
<body>

<section class="card card--front">
  <div class="brand-circle"></div>
  <div class="brand-name">TALKHARBOR</div>

  <div class="holder-name"><strong>MARCUS</strong> HALE</div>
  <div class="holder-role">Managing Director</div>

  <svg class="divider divider--icons" height="28" viewBox="0 0 364 28">
    <line x1="87" y1="14" x2="140" y2="14" stroke="var(--rule)" stroke-width="1.5"/>
    <line x1="224" y1="14" x2="277" y2="14" stroke="var(--rule)" stroke-width="1.5"/>
    <circle cx="154" cy="14" r="12" fill="var(--brand-blue)"/>
    <path d="M147 16 q7 -9 14 0 l-2 2 h-3 v-2 h-4 v2 h-3z" fill="#fff"/>
    <circle cx="181" cy="14" r="12" fill="var(--brand-blue)"/>
    <rect x="174" y="9" width="14" height="10" fill="#fff"/>
    <path d="M174 9 l7 6 l7 -6" fill="none" stroke="var(--brand-blue)" stroke-width="1.3"/>
    <circle cx="208" cy="14" r="12" fill="var(--brand-blue)"/>
    <circle cx="208" cy="14" r="7" fill="none" stroke="#fff" stroke-width="1.8"/>
    <line x1="201" y1="14" x2="215" y2="14" stroke="#fff" stroke-width="1.4"/>
    <line x1="208" y1="7" x2="208" y2="21" stroke="#fff" stroke-width="1.4"/>
  </svg>

  <ul class="contact-list">
    <li>020 7946 0123</li>
    <li>DaniaKV@talkharbor.co.uk</li>
    <li>www.TalkHarbor.co.uk</li>
  </ul>

  <svg class="divider divider--place" height="26" viewBox="0 0 364 26">
    <line x1="88" y1="13" x2="164" y2="13" stroke="var(--rule)" stroke-width="1.5"/>
    <line x1="201" y1="13" x2="283" y2="13" stroke="var(--rule)" stroke-width="1.5"/>
    <circle cx="182" cy="13" r="12" fill="var(--brand-blue)"/>
    <path d="M182 21 c-4 -5 -6 -8 -6 -11 a6 6 0 0 1 12 0 c0 3 -2 6 -6 11z" fill="#fff"/>
    <circle cx="182" cy="10" r="2.2" fill="var(--brand-blue)"/>
  </svg>
  <div class="location">London, UK</div>
</section>

<section class="card card--back">
  <svg class="back-mark" viewBox="0 0 369 380">
    <circle cx="184" cy="190" r="179" fill="var(--brand-deep)" stroke="var(--card-white)" stroke-width="22"/>
  </svg>
  <div class="back-name">TALKHARBOR</div>
  <div class="back-url">www.TalkHarbor.co.uk</div>
</section>

</body>
</html>
```